Brochure for a paper wholesaler who wants to educate his print industry clients

We will be making a stapled informative brochure, that contains basic information about our paper products - the types of paper there is, their characteristics and other useful information.
As we are part of a paper wholesaler group in Europe - ORVALT, we received a brochure in German that has this kind of information. The text in it is not as important. What is important is the layout of the document and how the text will appear in it (added in the uploaded files - 210915_Wiessenswertes_TBKU_H73.pdf).
We are allowed to tinker with this file and adjust it to our needs. So there are also .idml and .indd files available (also in the uploaded files).
We would like to keep the custom page size of 210 x290mm (8.3x11.4 in), or you can go up to 210x297mm (8.3x11.7 in).
What we want is a modern looking design that contains our companies red bordo and white/ grey colours to replace the existing green colours in this borchure. The pictures and appearance of the file can be changed according to your views and what you think would look good. We don't necessarily want to keep the same design, we just want the layout of the document be the same, as we will be placing our translated text into it. The ORVALT logo should be replaced with our own logo (KENDRO Logo.png).
As for how it could look, it could go together with our paper presentation, for which the design can be seen in the "KENDRO Base - v2.pptx".
Holiday season, so have a lot of tasks to take care of and not as much time to check MakerHive as often.

```html
<!DOCTYPE html>
<html lang="de">
<head>
<meta charset="utf-8">
<title>KENDRO – Wissenswert! Broschürentitel</title>
<link href="https://fonts.googleapis.com/css2?family=Josefin+Sans:ital,wght@0,300;0,400;0,600;1,600&display=swap" rel="stylesheet">
<style>
  :root {
    --stage: #a8a8a8;
    --paper: #f4f2f1;
    --paper-shade: #e6e3e2;
    --blush: #f3c3c0;
    --blush-deep: #e89f9c;
    --rose-band: #d9807d;
    --ink: #3a3536;
    --bordo: #8e2a35;
  }
  * { margin: 0; padding: 0; box-sizing: border-box; }
  html, body {
    width: 1200px;
    height: 900px;
    overflow: hidden;
    background: var(--stage);
  }
  .canvas {
    position: relative;
    width: 1200px;
    height: 900px;
  }
  .cover {
    position: absolute;
    left: 296px;
    top: 30px;
    width: 608px;
    height: 840px;
    background: var(--paper);
    overflow: hidden;
    font-family: "Josefin Sans", sans-serif;
  }
  .cover__visual {
    position: absolute;
    inset: 0;
    background:
      linear-gradient(135deg,
        transparent 0%, transparent 38%,
        rgba(217,128,125,0.55) 44%, rgba(232,159,156,0.25) 50%, transparent 56%),
      linear-gradient(135deg,
        var(--paper) 0%, var(--paper-shade) 35%,
        var(--blush-deep) 48%, var(--blush) 60%, var(--blush) 100%);
    transform-origin: center;
  }
  .cover__visual--flip {
    background: linear-gradient(225deg, var(--blush) 0%, var(--blush) 40%, var(--blush-deep) 55%, var(--paper-shade) 62%, var(--paper) 80%, var(--paper) 100%);
  }
  .brand {
    position: absolute;
    top: 58px;
    left: 50%;
    transform: translateX(-50%);
    display: flex;
    flex-direction: column;
    align-items: center;
    gap: 12px;
    color: var(--ink);
  }
  .brand__mark {
    width: 30px;
    height: 30px;
    border: 1.5px solid var(--ink);
  }
  .brand__name {
    font-weight: 300;
    font-size: 15px;
    letter-spacing: 0.55em;
    margin-right: -0.55em;
  }
  .headline {
    position: absolute;
    left: 56px;
    top: 612px;
    right: 40px;
  }
  .headline__kicker {
    display: inline-block;
    font-weight: 300;
    font-size: 11px;
    letter-spacing: 0.08em;
    color: var(--bordo);
    padding-bottom: 4px;
    border-bottom: 2px solid var(--bordo);
    margin-bottom: 12px;
  }
  .headline__title {
    font-weight: 400;
    font-size: 30px;
    line-height: 1.02;
    letter-spacing: 0.02em;
    color: var(--ink);
    text-transform: uppercase;
  }
  .headline__sub {
    margin-top: 14px;
    font-weight: 600;
    font-style: italic;
    font-size: 12px;
    letter-spacing: 0.03em;
    color: var(--bordo);
  }
</style>
</head>
<body>
  <main class="canvas">
    <article class="cover">
      <div class="cover__visual cover__visual--flip" role="img" aria-label="Fotografie gestaffelter Papierbögen in Rosé und Weiß mit diagonalen Kanten"></div>

      <div class="brand">
        <span class="brand__mark"></span>
        <span class="brand__name">KENDRO</span>
      </div>

      <header class="headline">
        <span class="headline__kicker">PAPER &amp; PRINT</span>
        <h1 class="headline__title">Wissenswert!<br>Formate, Klassen,<br>Farben, Berechnungen</h1>
        <p class="headline__sub">Wegweiser für den Umgang mit Papier und Karton</p>
      </header>
    </article>
  </main>
</body>
</html>
```